Commercial Auto Insurance Application and Commercial Property Insurance Application

Hi I need a fillable application for my business to send to potential clients for Commercial Auto Insurance and Commercial Property Insurance. I have attached an example application I currently use for another line of insurance.
Commercial Auto Insurance Application
On the first page I would need the following:
- Business Name: (fill in area for text)
- Effective Date: (fill in area for text)
- How do you structure your business? (Check box for “Sole Proprietor”, “Partnership”, “Corporation”, “LLC”)
- Contact Name: (fill in area for text) / Phone Number: (fill in area for text) / Contact Email (fill in area for text)
- Mailing address: (fill in area for text)
- Garaging location: (fill in area for text)
- Owner Name: (fill in area for text)
- Description of Operations: (fill in area for text)
- How long has the operation been in business? (fill in area for text)
- How many years of experience does your management have in the truck/transportation industry? (fill in area for text)
Coverages
Liability Combined Single Limit: ($1,000,000 (checkbox) / $500,000 (checkbox / $300,000 (checkbox) / Other: (fill in area for text)
Uninsured Motorist CSL: (fill in area for text) (checkbox for “Rejected”)
Medical Payments: (fill in area for text)
Physical Damage: (fill in area for text) (checkbox for Rejected)
Liability Deducible: ($500 checkbox, $1,000 checkbox, $2,500 checkbox, $5,000 checkbox)
Physical Damage Deductible: ($500 checkbox, $1,000 checkbox, $2,500 checkbox, $5,000 checkbox)
Driving radius: (fill in area for text)
How many years have you had your own continuous commercial auto insurance coverage for the current business name? (fill in area for text)
Do any of your vehicles travel across state lines? Yes (checkbox)/ No (checkbox)
If yes, please list all states in which vehicles operate: (fill in area for text)
What is the maximum radius traveled for your customer's business?
0-25 miles (checkbox)
26-50 miles (checkbox)
51-75 miles (checkbox)
76-100 miles (checkbox)
101-150 miles (checkbox)
151-200 miles (checkbox)
201-300 miles (checkbox)
300+ miles (checkbox)
Would you like physical damage coverage for this vehicle? (should be for each vehicle listed)
On the 2nd page of the application I would need the following:
I would need to have it where people can fill in the vehicle information such as VIN:, Year:, Make:, Model:, Type of Vehicle:, Trailers:, Value:
I would also need to have it where people can fill in the drivers with their driver info including Name:, DOB:, DL #:, DL State:, Class of License:, Married: Yes/No, Number of years driving similar vehicle:
Please make it where you can fill in 20 vehicle's information and 20 driver's info.
For the 2nd Application I would need one for Property Insurance
On the Commercial Property Application I would need the following:
- Building Address: (fill in area for text)
- Building Description: (fill in area for text)
- Building Amount: $(fill in area for text)
- Business Personal Property Amount: $ (fill in area for text) (checkbox for Not Needed)
- Building Sq Ft: (fill in area for text)
- Total Area Sq Ft: (fill in area for text)
- Building Construction Type: Wood Frame (checkbox), Steel (checkbox), Fire Resistive (checkbox), Non-Combustible (checkbox), Other (fill in area for text)
- # of stories: (fill in area for text)
- Year Built: (fill in area for text)
- Wiring improvement year: (fill in area for text)
- Roofing improvement year: (fill in area for text)
- Plumbing improvement year: (fill in area for text)
- Heating improvement year: (fill in area for text)
- What is to the right of the building and distance: (fill in area for text)
- What is to the left of the building and distance: (fill in area for text)
- What is in front of the building and distance: (fill in area for text)
- What is behind the building and distance: (fill in area for text)
- Burglar alarm installation and serviced by: (fill in area for text) None (checkbox)
- Does the premises have fire protection? Sprinkler system (checkbox), Fire detection (checkbox), Other: (fill in area for text) None (checkbox)

```html
<!DOCTYPE html>
<html lang="en">
<head>
<meta charset="utf-8">
<title>Commercial Auto Insurance Application</title>
<link rel="stylesheet" href="https://fonts.googleapis.com/css2?family=Montserrat:wght@800&family=Roboto:wght@400;500;700&display=swap">
<style>
:root{
  --navy:#0b2b7c;
  --green:#149a3b;
  --backdrop:#666666;
  --page:#f2f2f4;
  --field:#ffffff;
  --line:#e2e4ea;
  --stripe:#eef3fb;
  --ink:#2b2d33;
  --ink-strong:#15171c;
}
*{box-sizing:border-box;margin:0;padding:0}
html,body{width:1200px;height:971px;overflow:hidden;background:var(--backdrop)}
body{position:relative;font-family:'Roboto',Arial,sans-serif;color:var(--ink)}
.page{position:absolute;top:36px;width:546px;height:898px;background:var(--page);box-shadow:0 2px 10px rgba(0,0,0,.25)}
.page--form{left:40px}
.page--lists{left:614px}
.header-band{position:absolute;left:0;top:0}
.brand{position:absolute;left:24px;top:40px;color:var(--navy);font-weight:700;line-height:1}
.brand__name{display:block;font-size:18.5px;letter-spacing:.2px}
.brand__tag{display:block;font-size:7.5px;letter-spacing:3.1px;margin-top:5px}
.doc-title{position:absolute;left:231px;top:28px;font-family:'Montserrat',Arial,sans-serif;font-weight:800;font-size:19.5px;line-height:23.5px;color:#fff;letter-spacing:.3px}
.lbl{position:absolute;font-size:8px;line-height:10px;color:var(--ink)}
.field{position:absolute;height:17px;background:var(--field);border:1px solid var(--line);border-radius:2px}
.field--area{height:35px}
.chk{position:absolute;display:flex;align-items:center;gap:7px;height:12px;font-size:9px;font-weight:500;color:var(--ink-strong);white-space:nowrap}
.chk::before{content:"";width:9px;height:9px;background:var(--field);border:1px solid #d8dae0;border-radius:1.5px;flex:none}
.chk--plain::before{display:none}
.section-tab{position:absolute;left:0;top:400px;width:123px;height:28px}
.section-tab span{position:absolute;left:25px;top:6px;color:#fff;font-weight:700;font-size:12.5px}
.panel{position:absolute;left:25px;width:497px;height:345px;background:#fff;border-radius:9px}
.pill{position:absolute;left:39px;width:127px;height:27px;border-radius:14px;background:var(--green);color:#fff;font-weight:700;font-size:10.5px;display:flex;align-items:center;justify-content:center}
.grid{position:absolute;left:39px;width:468px;border-collapse:collapse;table-layout:fixed}
.grid th{background:var(--navy);color:#fff;font-size:8.5px;font-weight:500;height:21px;padding:0;text-align:center;border-right:1px solid #2c4c9c;white-space:nowrap;overflow:hidden}
.grid th:first-child{border-top-left-radius:3px}
.grid th:last-child{border-top-right-radius:3px;border-right:none}
.grid td{height:21.7px;border:1px solid var(--line);background:#fff}
.grid tr:nth-child(even) td{background:var(--stripe)}
</style>
</head>
<body>

<section class="page page--form">
  <svg class="header-band" width="546" height="90" viewBox="0 0 546 90" aria-hidden="true">
    <polygon points="208,18 546,18 546,21 207,21" fill="var(--green)"/>
    <polygon points="206,24 546,24 546,80 185,80" fill="var(--navy)"/>
    <polygon points="184,82 546,82 546,86 182,86" fill="var(--green)"/>
  </svg>
  <div class="brand"><span class="brand__name">PRAIRIEVIEW</span><span class="brand__tag">INSURANCE SERVICES</span></div>
  <h1 class="doc-title">COMMERCIAL AUTO<br>INSURANCE APPLICATION</h1>

  <div class="lbl" style="left:24px;top:101px">Business Name</div>
  <div class="field" style="left:24px;top:116px;width:242px"></div>
  <div class="lbl" style="left:279px;top:101px">Effective Date</div>
  <div class="field" style="left:279px;top:116px;width:242px"></div>

  <div class="lbl" style="left:24px;top:147px">How do you structure your business?</div>
  <div class="chk" style="left:183px;top:146px">Partnership</div>
  <div class="chk" style="left:281px;top:146px">Sole Proprietor</div>
  <div class="chk" style="left:393px;top:146px">Corporation</div>
  <div class="chk" style="left:491px;top:146px">LLC</div>

  <div class="lbl" style="left:24px;top:169px">Contact Name</div>
  <div class="field" style="left:24px;top:184px;width:157px"></div>
  <div class="lbl" style="left:193px;top:169px">Phone Number</div>
  <div class="field" style="left:194px;top:184px;width:157px"></div>
  <div class="lbl" style="left:364px;top:169px">Contact Email</div>
  <div class="field" style="left:364px;top:184px;width:157px"></div>

  <div class="lbl" style="left:24px;top:214px">Owner Name</div>
  <div class="field" style="left:24px;top:230px;width:497px"></div>

  <div class="lbl" style="left:24px;top:259px">Description of Operations</div>
  <div class="field field--area" style="left:24px;top:275px;width:497px"></div>

  <div class="lbl" style="left:24px;top:328px">How long has the operation been in business?</div>
  <div class="field" style="left:24px;top:349px;width:242px"></div>
  <div class="lbl" style="left:279px;top:323px;width:245px">How many years of experience does your management have in the truck/transportation industry?</div>
  <div class="field" style="left:279px;top:349px;width:242px"></div>

  <svg class="section-tab" viewBox="0 0 123 28" aria-hidden="true"><polygon points="0,0 106,0 123,28 0,28" fill="var(--green)"/></svg>
  <div class="section-tab"><span>Coverages</span></div>

  <div class="lbl" style="left:24px;top:449px">How do you structure your business?</div>
  <div class="chk" style="left:173px;top:448px">$1,000,000</div>
  <div class="chk" style="left:255px;top:448px">$500,000</div>
  <div class="chk" style="left:331px;top:448px">$300,000</div>
  <div class="chk chk--plain" style="left:407px;top:448px">Other:</div>
  <div class="field" style="left:439px;top:446px;width:82px"></div>

  <div class="lbl" style="left:24px;top:478px">Uninsured Motorist CSL</div>
  <div class="field" style="left:24px;top:494px;width:196px"></div>
  <div class="chk" style="left:231px;top:496px">Rejected</div>
  <div class="lbl" style="left:295px;top:478px">Medical Payments</div>
  <div class="field" style="left:296px;top:494px;width:225px"></div>

  <div class="lbl" style="left:24px;top:528px">Liability Deductible</div>
  <div class="chk" style="left:149px;top:527px">$500</div>
  <div class="chk" style="left:227px;top:527px">$1,000</div>
  <div class="chk" style="left:312px;top:527px">$2,500</div>
  <div class="chk" style="left:397px;top:527px">$5,000</div>

  <div class="lbl" style="left:24px;top:555px">Physical Damage Deductible</div>
  <div class="chk" style="left:149px;top:554px">$500</div>
  <div class="chk" style="left:227px;top:554px">$1,000</div>
  <div class="chk" style="left:312px;top:554px">$2,500</div>
  <div class="chk" style="left:397px;top:554px">$5,000</div>

  <div class="lbl" style="left:24px;top:581px">Driving Radius</div>
  <div class="field" style="left:24px;top:596px;width:497px"></div>

  <div class="lbl" style="left:24px;top:629px">How many years have you had your own continuous commercial auto insurance coverage for the current business name?</div>
  <div class="field" style="left:24px;top:644px;width:497px"></div>

  <div class="lbl" style="left:24px;top:679px">Do any of your vehicles travel across state lines?</div>
  <div class="chk" style="left:226px;top:678px">Yes</div>
  <div class="chk" style="left:304px;top:678px">No</div>

  <div class="lbl" style="left:24px;top:704px">If yes, list all states:</div>
  <div class="field" style="left:24px;top:720px;width:497px"></div>

  <div class="lbl" style="left:24px;top:753px">Maximum radius traveled</div>
  <div class="chk" style="left:25px;top:771px">0-25 miles</div>
  <div class="chk" style="left:165px;top:771px">26-50 miles</div>
  <div class="chk" style="left:310px;top:771px">51-75 miles</div>
  <div class="chk" style="left:456px;top:771px">76-100 miles</div>
  <div class="chk" style="left:25px;top:788px">101-150 miles</div>
  <div class="chk" style="left:165px;top:788px">151-200 miles</div>
  <div class="chk" style="left:310px;top:788px">201-300 miles</div>
  <div class="chk" style="left:456px;top:788px">300+ miles</div>

  <div class="lbl" style="left:24px;top:815px">Would you like physical damage coverage for this vehicle?</div>
  <div class="chk" style="left:25px;top:835px">Vehicle Name 1</div>
  <div class="chk" style="left:129px;top:835px">Vehicle Name 2</div>
  <div class="chk" style="left:238px;top:835px">Vehicle Name 3</div>
  <div class="chk" style="left:344px;top:835px">Vehicle Name 4</div>
  <div class="chk" style="left:450px;top:835px">Vehicle Name 5</div>
  <div class="chk" style="left:25px;top:852px">Vehicle Name 6</div>
  <div class="chk" style="left:129px;top:852px">Vehicle Name 7</div>
  <div class="chk" style="left:238px;top:852px">Vehicle Name 8</div>
  <div class="chk" style="left:344px;top:852px">Vehicle Name 9</div>
  <div class="chk" style="left:450px;top:852px">Vehicle Name 10</div>
</section>

<section class="page page--lists">
  <svg class="header-band" width="546" height="90" viewBox="0 0 546 90" aria-hidden="true">
    <polygon points="208,18 546,18 546,21 207,21" fill="var(--green)"/>
    <polygon points="206,24 546,24 546,80 185,80" fill="var(--navy)"/>
    <polygon points="184,82 546,82 546,86 182,86" fill="var(--green)"/>
  </svg>
  <div class="brand"><span class="brand__name">PRAIRIEVIEW</span><span class="brand__tag">INSURANCE SERVICES</span></div>
  <h1 class="doc-title">COMMERCIAL AUTO<br>INSURANCE APPLICATION</h1>

  <div class="panel" style="top:129px"></div>
  <div class="pill" style="top:116px">Vehicle Information</div>
  <table class="grid" style="top:156px">
    <thead><tr><th>VIN</th><th>Year</th><th>Make</th><th>Model</th><th>Type of Vehicle</th><th>Trailers</th><th>Value</th></tr></thead>
    <tbody>
      <tr><td></td><td></td><td></td><td></td><td></td><td></td><td></td></tr>
      <tr><td></td><td></td><td></td><td></td><td></td><td></td><td></td></tr>
      <tr><td></td><td></td><td></td><td></td><td></td><td></td><td></td></tr>
      <tr><td></td><td></td><td></td><td></td><td></td><td></td><td></td></tr>
      <tr><td></td><td></td><td></td><td></td><td></td><td></td><td></td></tr>
      <tr><td></td><td></td><td></td><td></td><td></td><td></td><td></td></tr>
      <tr><td></td><td></td><td></td><td></td><td></td><td></td><td></td></tr>
      <tr><td></td><td></td><td></td><td></td><td></td><td></td><td></td></tr>
      <tr><td></td><td></td><td></td><td></td><td></td><td></td><td></td></tr>
      <tr><td></td><td></td><td></td><td></td><td></td><td></td><td></td></tr>
      <tr><td></td><td></td><td></td><td></td><td></td><td></td><td></td></tr>
      <tr><td></td><td></td><td></td><td></td><td></td><td></td><td></td></tr>
      <tr><td></td><td></td><td></td><td></td><td></td><td></td><td></td></tr>
    </tbody>
  </table>

  <div class="panel" style="top:520px"></div>
  <div class="pill" style="top:507px">Driver Information</div>
  <table class="grid" style="top:547px">
    <thead><tr><th>Names</th><th>DOB</th><th>DL #</th><th>DL State</th><th>Class of License</th><th>Married</th><th>Number of years</th></tr></thead>
    <tbody>
      <tr><td></td><td></td><td></td><td></td><td></td><td></td><td></td></tr>
      <tr><td></td><td></td><td></td><td></td><td></td><td></td><td></td></tr>
      <tr><td></td><td></td><td></td><td></td><td></td><td></td><td></td></tr>
      <tr><td></td><td></td><td></td><td></td><td></td><td></td><td></td></tr>
      <tr><td></td><td></td><td></td><td></td><td></td><td></td><td></td></tr>
      <tr><td></td><td></td><td></td><td></td><td></td><td></td><td></td></tr>
      <tr><td></td><td></td><td></td><td></td><td></td><td></td><td></td></tr>
      <tr><td></td><td></td><td></td><td></td><td></td><td></td><td></td></tr>
      <tr><td></td><td></td><td></td><td></td><td></td><td></td><td></td></tr>
      <tr><td></td><td></td><td></td><td></td><td></td><td></td><td></td></tr>
      <tr><td></td><td></td><td></td><td></td><td></td><td></td><td></td></tr>
      <tr><td></td><td></td><td></td><td></td><td></td><td></td><td></td></tr>
      <tr><td></td><td></td><td></td><td></td><td></td><td></td><td></td></tr>
    </tbody>
  </table>
</section>

</body>
</html>
```